Business Cards for a law firm

Business cards for our law firm. Use our silhoette logo and OAK PARTNERS - check our website (www.oakpartners.example)

Contact Information for Business Card

our silhouette logo, OAK PARTNERS, 800-555-0147, Dorian Pemberton, dorian@oakpartners.example

Requirements
Must have
• our silhouette logo, OAK PARTNERS, 800-555-0147, Dorian Pemberton, dorian@oakpartners.example

```html
<!DOCTYPE html>
<html lang="en">
<head>
<meta charset="utf-8">
<title>Oak Partners — Business Cards</title>
<link href="https://fonts.googleapis.com/css2?family=Montserrat:wght@400;700&display=swap" rel="stylesheet">
<style>
  :root {
    --page: #e3e7ea;
    --navy: #22336a;
    --navy-deep: #1b2858;
    --navy-shade: #172250;
    --sky: #3f97d4;
    --white: #ffffff;
  }
  * { margin: 0; padding: 0; box-sizing: border-box; }
  html, body {
    width: 1200px; height: 960px; overflow: hidden;
    background: var(--page);
    font-family: "Montserrat", Arial, sans-serif;
  }
  .canvas { position: relative; width: 1200px; height: 960px; }
  .card {
    position: absolute; left: 249px; width: 702px; height: 401px;
    border-radius: 28px; overflow: hidden; background: var(--navy);
    color: var(--white);
  }
  .card--front { top: 58px; }
  .card--back { top: 501px; }

  /* Front */
  .front-pattern {
    position: absolute; inset: 0;
    background:
      radial-gradient(ellipse 70% 60% at 95% 5%, rgba(63,151,212,0.85), rgba(63,151,212,0) 70%),
      linear-gradient(180deg, #263a78 0%, var(--navy) 55%, var(--navy-deep) 100%);
  }
  .front-brand {
    position: absolute; left: 163px; top: 150px;
    display: flex; align-items: center; gap: 20px;
  }
  .brand-square { width: 64px; height: 64px; background: var(--white); }
  .front-name {
    font-weight: 400; font-size: 45px; line-height: 40px;
    letter-spacing: 1px; text-transform: uppercase; color: var(--white);
  }

  /* Back */
  .back-shape { position: absolute; inset: 0; }
  .back-figures {
    position: absolute; left: 472px; top: 28px; width: 230px; height: 345px;
    background: linear-gradient(160deg, #3f97d4 0%, #2f5fa6 40%, var(--navy-deep) 75%);
    border-radius: 40px 40px 0 0;
    opacity: 0.9;
  }
  .back-brand {
    position: absolute; left: 36px; top: 30px;
    display: flex; align-items: center; gap: 14px;
  }
  .brand-square--small { width: 34px; height: 34px; }
  .back-name {
    font-size: 27px; font-weight: 400; letter-spacing: 1.5px;
    text-transform: uppercase; color: var(--white);
  }
  .person {
    position: absolute; left: 23px; top: 226px;
    font-size: 30px; letter-spacing: 1.5px; text-transform: uppercase;
  }
  .person-first { font-weight: 700; }
  .person-last { font-weight: 400; }
  .contacts {
    position: absolute; left: 23px; top: 299px; list-style: none;
  }
  .contact {
    display: flex; align-items: center; height: 22px; margin-bottom: 1px;
    font-size: 16px; letter-spacing: 1px; text-transform: uppercase;
  }
  .contact--phone { font-size: 19px; height: 26px; margin-bottom: 0; }
  .contact-icon { width: 16px; height: 16px; margin-right: 17px; flex: none; }
</style>
</head>
<body>
<main class="canvas">

  <section class="card card--front" aria-label="Card front">
    <div class="front-pattern" role="img" aria-label="Repeating grid of paired silhouette figures fading from light blue to navy"></div>
    <div class="front-brand">
      <span class="brand-square"></span>
      <p class="front-name">Oak<br>Partners</p>
    </div>
  </section>

  <section class="card card--back" aria-label="Card back">
    <div class="back-figures" role="img" aria-label="Large illustration of two standing figures in blue gradient"></div>
    <svg class="back-shape" width="702" height="401" viewBox="0 0 702 401" aria-hidden="true">
      <defs>
        <filter id="panel-shadow" x="-10%" y="-10%" width="130%" height="120%">
          <feDropShadow dx="6" dy="0" stdDeviation="6" flood-color="#0e1840" flood-opacity="0.55"/>
        </filter>
      </defs>
      <path d="M0,0 H363 Q562,200 357,401 H0 Z" fill="#22336a" filter="url(#panel-shadow)"/>
    </svg>

    <div class="back-brand">
      <span class="brand-square brand-square--small"></span>
      <p class="back-name">Oak Partners</p>
    </div>

    <p class="person"><span class="person-first">Dorian</span> <span class="person-last">Pemberton</span></p>

    <ul class="contacts">
      <li class="contact contact--phone">
        <svg class="contact-icon" viewBox="0 0 16 16" aria-hidden="true"><path d="M3 1.5 L5.5 1 L7 4.5 L5.3 5.8 Q6.5 8.8 9.8 10.5 L11.2 8.8 L14.5 10.3 L14 13 Q13 15 10.5 14.2 Q4 12 1.8 5.3 Q1.2 2.5 3 1.5 Z" fill="#ffffff"/></svg>
        800-555-0147
      </li>
      <li class="contact">
        <svg class="contact-icon" viewBox="0 0 16 16" aria-hidden="true"><circle cx="8" cy="8" r="7" fill="none" stroke="#ffffff" stroke-width="1.4"/><ellipse cx="8" cy="8" rx="3" ry="7" fill="none" stroke="#ffffff" stroke-width="1.2"/><path d="M1 8 H15" stroke="#ffffff" stroke-width="1.2"/></svg>
        www.oakpartners.example
      </li>
      <li class="contact">
        <svg class="contact-icon" viewBox="0 0 16 16" aria-hidden="true"><rect x="1" y="4" width="14" height="10" fill="none" stroke="#ffffff" stroke-width="1.4"/><path d="M1 4 L8 10 L15 4" fill="none" stroke="#ffffff" stroke-width="1.4"/></svg>
        dorian@oakpartners.example
      </li>
    </ul>
  </section>

</main>
</body>
</html>
```